Modern Verdell Tree Care Website

I need a website for a full service Tree Care company. The company provides tree pruning, tree removal, tree preservation, emergency services, stump grinding, and emergency tree services.

Target Market(s)

Customers that need tree services

Industry/Entity Type

Landscaping, Tree Services

Coding

Coded - Design and coding required

Number of Pages Required

5+ page

Font styles to use
Sans Serif

Requirements
Must have
• Good clean design that showcases the services the company provides.
Nice to have
• Services page; contact form, blog, home page, about page

```html
<!DOCTYPE html>
<html lang="en">
<head>
<meta charset="utf-8">
<title>Verdell Tree Care</title>
<link href="https://fonts.googleapis.com/css2?family=Exo+2:wght@400;500;600;700&family=Mulish:wght@400;600;700&display=swap" rel="stylesheet">
<style>
:root{
  --green:#7dc242;
  --orange:#f8a735;
  --tan:#c59a6b;
  --slate:#667473;
  --ink:#1e1e1e;
  --muted:#4a4a4a;
  --dark:#1b2118;
  --white:#ffffff;
  --light:#f3f4f1;
}
*{box-sizing:border-box;margin:0;padding:0}
html,body{width:1200px;height:4181px;overflow:hidden;background:var(--white)}
body{font-family:"Mulish",sans-serif;color:var(--ink)}
.page{position:relative;width:1200px;height:4181px;overflow:hidden}
.abs{position:absolute}
.head-font{font-family:"Exo 2",sans-serif}
.btn{position:absolute;display:flex;align-items:center;justify-content:center;background:var(--orange);color:var(--ink);font-family:"Exo 2",sans-serif;font-weight:500;text-transform:uppercase;letter-spacing:.3px}
.section-title{position:absolute;left:0;width:1200px;text-align:center;font-family:"Exo 2",sans-serif;font-weight:600;font-size:35px;letter-spacing:1.5px;text-transform:uppercase}
.rule{position:absolute;height:2px;width:36px;left:582px}

/* header */
.brand{position:absolute;left:130px;top:46px;display:flex;align-items:center;gap:14px}
.brand-mark{width:52px;height:52px;background:var(--green)}
.brand-name{font-family:"Exo 2",sans-serif;font-weight:700;font-size:34px;color:var(--slate);letter-spacing:1px;line-height:1}
.call{position:absolute;left:859px;top:34px;display:flex;gap:14px;align-items:center}
.call-icon{width:34px;height:34px;background:#5b6564;display:flex;align-items:center;justify-content:center}
.call-label{font-size:11px;color:var(--ink);letter-spacing:.5px}
.call-num{font-family:"Exo 2",sans-serif;font-size:20px;color:var(--ink);letter-spacing:.5px}
.nav{position:absolute;top:98px;font-family:"Exo 2",sans-serif;font-size:15px;color:var(--ink)}
.nav.active{color:var(--green);padding-bottom:6px;border-bottom:2px solid var(--green)}

/* hero */
.hero-photo{position:absolute;left:0;top:150px;width:1200px;height:580px;background:linear-gradient(100deg,#3f4f2a 0%,#5b6a35 30%,#6f6a43 55%,#a8763f 72%,#4e6a2b 100%)}
.hero-title{position:absolute;left:133px;top:268px;font-family:"Exo 2",sans-serif;font-weight:500;font-size:70px;line-height:78px;color:var(--white);letter-spacing:2px}
.hero-text{position:absolute;left:140px;top:444px;font-size:22px;line-height:29px;color:var(--white)}
.dots{position:absolute;top:652px;left:558px;display:flex;gap:12px}
.dot{width:12px;height:12px;border-radius:50%;background:var(--white)}
.dot.on{background:var(--orange)}

/* services */
.card{position:absolute;top:971px;width:210px;height:257px;border:1.5px solid #a9d88a;background:var(--white)}
.card-tri{position:absolute;top:888px;width:118px;height:122px}
.card h3{position:absolute;top:70px;left:0;width:100%;text-align:center;font-family:"Exo 2",sans-serif;font-weight:600;font-size:15.5px;letter-spacing:.3px}
.card p{position:absolute;top:111px;left:8px;right:8px;text-align:center;font-size:12px;line-height:17.5px;color:var(--muted)}
.card .btn{top:196px;left:55px;width:90px;height:30px;font-size:11px}
.arrow{position:absolute}

/* who */
.who-bg{position:absolute;left:0;top:1377px;width:1200px;height:520px;background:var(--slate)}
.who-photo{position:absolute;left:0;top:1377px;width:700px;height:520px;background:linear-gradient(90deg,#5e4a32 0%,#7a6040 35%,#8a7658 60%,rgba(102,116,115,0) 100%)}
.who-title{position:absolute;left:635px;top:1445px;font-family:"Exo 2",sans-serif;font-weight:500;font-size:34px;color:var(--white);letter-spacing:1.5px}
.who-text{position:absolute;left:635px;width:428px;font-size:14px;line-height:21px;color:#eef0ef;text-align:justify}

/* why */
.why-label{position:absolute;font-family:"Exo 2",sans-serif;font-size:17px;line-height:24px;color:var(--ink)}
.why-dot{position:absolute;width:78px;height:78px;border-radius:50%;background:var(--tan)}
.why-dot::after{content:"";position:absolute;inset:16px;border:2px solid rgba(255,255,255,.85);border-radius:50%}

/* blog */
.blog-bg{position:absolute;left:0;top:2566px;width:1200px;height:658px;background:linear-gradient(180deg,#1c2118 0%,#2a3322 45%,#1a1f16 100%)}
.post{position:absolute;top:2751px;width:296px;height:408px;background:var(--white)}
.post-img{position:absolute;left:0;top:0;width:296px;height:172px}
.post-date{position:absolute;left:28px;top:160px;background:var(--tan);color:var(--white);font-size:12px;padding:4px 12px}
.post h3{position:absolute;left:28px;top:210px;width:250px;font-family:"Exo 2",sans-serif;font-weight:600;font-size:16px;line-height:23px}
.post p{position:absolute;left:28px;top:268px;width:250px;font-size:11.5px;line-height:17.5px;color:var(--muted)}
.post .btn{left:28px;top:350px;width:90px;height:29px;font-size:11px}

/* appointment */
.appt-bg{position:absolute;left:0;top:3224px;width:1200px;height:552px;background:var(--light)}
.appt-box{position:absolute;left:131px;top:3310px;width:936px;height:377px;background:linear-gradient(135deg,#16301a 0%,#23502a 45%,#153019 100%)}

/* footer */
.foot{position:absolute;left:0;top:3776px;width:1200px;height:349px;background:var(--slate)}
.foot-nav{position:absolute;top:4007px;font-family:"Exo 2",sans-serif;font-size:15px;color:var(--white)}
.social{width:25px;height:25px;border-radius:50%;background:var(--white)}
.copy{position:absolute;left:0;top:4125px;width:1200px;height:56px;background:var(--tan);display:flex;align-items:center;justify-content:center;font-family:"Exo 2",sans-serif;font-size:14px;color:var(--ink)}
</style>
</head>
<body>
<div class="page">

  <!-- Header -->
  <header>
    <div class="brand"><span class="brand-mark"></span><span class="brand-name">Verdell Tree Care</span></div>
    <div class="btn" style="left:653px;top:35px;width:185px;height:38px;font-size:14px;color:var(--white)">Get Free Estimate</div>
    <div class="call">
      <div class="call-icon">
        <svg width="18" height="18" viewBox="0 0 24 24"><path fill="#fff" d="M6.6 10.8a15.1 15.1 0 0 0 6.6 6.6l2.2-2.2c.3-.3.7-.4 1-.2 1.1.4 2.3.6 3.6.6.6 0 1 .4 1 1V20c0 .6-.4 1-1 1A17 17 0 0 1 3 4c0-.6.4-1 1-1h3.5c.6 0 1 .4 1 1 0 1.3.2 2.5.6 3.6.1.3 0 .7-.2 1z"/></svg>
      </div>
      <div><div class="call-label">CALL US</div><div class="call-num">(555) 214 - 7730</div></div>
    </div>
    <nav>
      <span class="nav active" style="left:577px">HOME</span>
      <span class="nav" style="left:661px">ABOUT US</span>
      <span class="nav" style="left:778px">SERVICES</span>
      <span class="nav" style="left:893px">BLOG</span>
      <span class="nav" style="left:974px">CONTACT US</span>
    </nav>
  </header>

  <!-- Hero -->
  <section>
    <div class="hero-photo" role="img" aria-label="Arborist in a safety helmet cutting a tree trunk with a chainsaw in a green forest"></div>
    <h1 class="hero-title">TREE<br>REMOVAL</h1>
    <p class="hero-text">Lorem Ipsum is simply dummy text<br>of the printing and typesetting.</p>
    <div class="btn" style="left:143px;top:531px;width:229px;height:50px;font-size:18px">Get Free Estimate</div>
    <div class="dots"><span class="dot on"></span><span class="dot"></span><span class="dot"></span><span class="dot"></span></div>
    <svg class="abs" style="left:0;top:700px" width="1200" height="30" viewBox="0 0 1200 30"><path fill="#fff" d="M0 22 L40 14 L70 20 L110 10 L150 18 L200 12 L240 22 L290 14 L330 19 L380 9 L430 17 L470 12 L520 21 L570 13 L610 18 L660 10 L700 19 L750 13 L800 20 L840 11 L890 18 L930 14 L980 21 L1030 12 L1070 19 L1120 13 L1160 20 L1200 14 L1200 30 L0 30 Z"/></svg>
  </section>

  <!-- Services -->
  <section>
    <svg class="abs" style="left:0;top:723px" width="1200" height="265" viewBox="0 0 1200 265">
      <polygon points="0,0 130,0 0,262" fill="#c59a6b"/>
      <polygon points="1072,0 1200,0 1200,262" fill="#f8a735"/>
    </svg>
    <h2 class="section-title" style="top:774px;color:var(--ink)">Our Services</h2>
    <div class="rule" style="top:848px;background:var(--ink)"></div>

    <svg class="arrow" style="left:58px;top:1076px" width="24" height="40" viewBox="0 0 24 40"><path d="M20 2 L4 20 L20 38" stroke="#9aa3a2" stroke-width="2" fill="none"/></svg>
    <svg class="arrow" style="left:1107px;top:1076px" width="24" height="40" viewBox="0 0 24 40"><path d="M4 2 L20 20 L4 38" stroke="#9aa3a2" stroke-width="2" fill="none"/></svg>

    <div class="card" style="left:131px"><h3>TREE TRIMMING</h3><p>Lorem ipsum dolor sit amet, consectetur adipiscing elit, sed do eiusmod tempor incididunt ut labore et dolore.</p><div class="btn">Read More</div></div>
    <div class="card" style="left:375px"><h3>TREE REMOVAL</h3><p>Lorem ipsum dolor sit amet, consectetur adipiscing elit, sed do eiusmod tempor incididunt ut labore et dolore.</p><div class="btn">Read More</div></div>
    <div class="card" style="left:614px"><h3>TREE CLEARING</h3><p>Lorem ipsum dolor sit amet, consectetur adipiscing elit, sed do eiusmod tempor incididunt ut labore et dolore.</p><div class="btn">Read More</div></div>
    <div class="card" style="left:857px"><h3>STUMP GRINDING</h3><p>Lorem ipsum dolor sit amet, consectetur adipiscing elit, sed do eiusmod tempor incididunt ut labore et dolore.</p><div class="btn">Read More</div></div>

    <svg class="card-tri" style="left:177px" viewBox="0 0 118 122"><polygon points="59,0 118,122 0,122" fill="#7dc242"/></svg>
    <svg class="card-tri" style="left:421px" viewBox="0 0 118 122"><polygon points="59,0 118,122 0,122" fill="#7dc242"/></svg>
    <svg class="card-tri" style="left:660px" viewBox="0 0 118 122"><polygon points="59,0 118,122 0,122" fill="#7dc242"/></svg>
    <svg class="card-tri" style="left:903px" viewBox="0 0 118 122"><polygon points="59,0 118,122 0,122" fill="#7dc242"/></svg>

    <div class="btn" style="left:508px;top:1283px;width:181px;height:44px;font-size:13px;background:var(--white);border:1.5px solid var(--tan);color:var(--tan)">View All Services</div>
  </section>

  <!-- Who we are -->
  <section>
    <div class="who-bg"></div>
    <div class="who-photo" role="img" aria-label="Stump grinder cutting into a large tree stump with sawdust flying, pine trees behind"></div>
    <svg class="abs" style="left:0;top:1372px" width="1200" height="22" viewBox="0 0 1200 22"><path fill="#fff" d="M0 0 L1200 0 L1200 8 L1150 14 L1110 6 L1060 13 L1010 7 L960 15 L910 8 L860 12 L810 5 L760 14 L710 9 L660 15 L610 6 L560 13 L510 8 L460 16 L410 7 L360 13 L310 6 L260 15 L210 9 L160 14 L110 6 L60 13 L0 8 Z"/></svg>
    <svg class="abs" style="left:0;top:1880px" width="1200" height="22" viewBox="0 0 1200 22"><path fill="#fff" d="M0 22 L1200 22 L1200 12 L1150 6 L1100 14 L1050 8 L1000 15 L950 6 L900 13 L850 7 L800 16 L750 8 L700 13 L650 5 L600 14 L550 8 L500 15 L450 7 L400 12 L350 5 L300 14 L250 8 L200 15 L150 6 L100 13 L50 7 L0 12 Z"/></svg>
    <h2 class="who-title">WHO WE ARE</h2>
    <div class="rule" style="top:1507px;left:637px;width:68px;background:var(--white)"></div>
    <p class="who-text" style="top:1546px">At Verdell Tree Care, we are more than just a tree service company, we are stewards of our beautiful trees. With a passion deeply rooted in arboriculture, we embark on a mission to promote the health, beauty, and safety of your trees and landscapes.</p>
    <p class="who-text" style="top:1671px">Whether it's expert tree trimming to enhance aesthetics, meticulous tree removal to mitigate hazards, or comprehensive tree health assessments to ensure safety, we approach each task with unwavering dedication and attention to detail.</p>
    <div class="btn" style="left:635px;top:1785px;width:128px;height:47px;font-size:15px">Read More</div>
  </section>

  <!-- Why choose us -->
  <section>
    <h2 class="section-title" style="top:1958px;color:var(--ink)">Why Choose Us</h2>
    <div class="rule" style="top:2030px;background:var(--ink)"></div>
    <svg class="abs" style="left:0;top:2100px" width="1200" height="460" viewBox="0 2100 1200 460">
      <path d="M 399 2520 A 228 228 0 1 1 803 2520" fill="none" stroke="#9ea3a3" stroke-width="2"/>
      <path d="M 387 2534 A 244 244 0 1 1 815 2534" fill="none" stroke="#9ea3a3" stroke-width="2"/>
    </svg>
    <div class="abs" style="left:480px;top:2330px;width:242px;text-align:center;font-family:'Exo 2',sans-serif;font-weight:600;font-size:32px;line-height:40px;color:var(--green)">Verdell<br>Tree Care</div>

    <div class="why-dot" style="left:562px;top:2126px"></div>
    <div class="why-dot" style="left:416px;top:2170px"></div>
    <div class="why-dot" style="left:706px;top:2170px"></div>
    <div class="why-dot" style="left:341px;top:2277px"></div>
    <div class="why-dot" style="left:781px;top:2277px"></div>
    <div class="why-dot" style="left:335px;top:2410px"></div>
    <div class="why-dot" style="left:788px;top:2410px"></div>

    <div class="why-label" style="left:451px;top:2083px;width:300px;text-align:center">Professional Work</div>
    <div class="why-label" style="left:195px;top:2168px;width:200px;text-align:right">Locally Owned &amp;<br>Operated</div>
    <div class="why-label" style="left:812px;top:2171px">Safety is Our<br>No.1 Priority</div>
    <div class="why-label" style="left:115px;top:2285px;width:200px;text-align:right">24- Hours<br>Emergency Services</div>
    <div class="why-label" style="left:887px;top:2301px">Free Estimates</div>
    <div class="why-label" style="left:110px;top:2423px;width:200px;text-align:right">Licensed and<br>Insured</div>
    <div class="why-label" style="left:890px;top:2425px">Licensed<br>Arborist on Staff</div>
  </section>

  <!-- Blog -->
  <section>
    <div class="blog-bg" role="img" aria-label="Dark photo of a forest with tree workers in the background"></div>
    <svg class="abs" style="left:0;top:2560px" width="1200" height="24" viewBox="0 0 1200 24"><path fill="#fff" d="M0 0 L1200 0 L1200 10 L1150 16 L1100 7 L1050 14 L1000 8 L950 17 L900 9 L850 14 L800 6 L750 15 L700 10 L650 17 L600 7 L550 14 L500 9 L450 17 L400 8 L350 14 L300 7 L250 16 L200 10 L150 15 L100 7 L50 14 L0 9 Z"/></svg>
    <svg class="abs" style="left:0;top:3200px" width="1200" height="24" viewBox="0 0 1200 24"><path fill="#fff" d="M0 24 L1200 24 L1200 12 L1150 7 L1100 15 L1050 8 L1000 16 L950 7 L900 14 L850 8 L800 17 L750 9 L700 14 L650 6 L600 15 L550 9 L500 16 L450 8 L400 13 L350 6 L300 15 L250 9 L200 16 L150 7 L100 14 L50 8 L0 13 Z"/></svg>
    <h2 class="section-title" style="top:2632px;color:var(--white)">Latest Blog</h2>
    <div class="rule" style="top:2699px;background:var(--white)"></div>

    <svg class="arrow" style="left:56px;top:2928px" width="26" height="48" viewBox="0 0 26 48"><path d="M22 2 L4 24 L22 46" stroke="#fff" stroke-width="2.5" fill="none"/></svg>
    <svg class="arrow" style="left:1116px;top:2928px" width="26" height="48" viewBox="0 0 26 48"><path d="M4 2 L22 24 L4 46" stroke="#fff" stroke-width="2.5" fill="none"/></svg>

    <article class="post" style="left:131px">
      <div class="post-img" role="img" aria-label="Stump grinder chewing through a tree stump" style="background:linear-gradient(135deg,#8a7a5c,#5d4c33 60%,#3e3524)"></div>
      <span class="post-date">12 June 2024</span>
      <h3>Lorem ipsum dolor sit amet consectetur adipiscing</h3>
      <p>Lorem ipsum dolor sit amet, conse ctetur adipiscing elit, sed do eiusmod tempor incididunt. laboris nisi ut aliquip ex ea commodo consequat.</p>
      <div class="btn">Read More</div>
    </article>
    <article class="post" style="left:453px">
      <div class="post-img" role="img" aria-label="Climber roped into a bare tree against a pale sky" style="background:linear-gradient(180deg,#d9dcd8,#9a8f7e 70%,#6b5e4a)"></div>
      <span class="post-date">12 June 2024</span>
      <h3>Lorem ipsum dolor sit amet consectetur adipiscing</h3>
      <p>Lorem ipsum dolor sit amet, conse ctetur adipiscing elit, sed do eiusmod tempor incididunt. laboris nisi ut aliquip ex ea commodo consequat.</p>
      <div class="btn">Read More</div>
    </article>
    <article class="post" style="left:771px">
      <div class="post-img" role="img" aria-label="Arborist climbing a leafy tree in summer" style="background:linear-gradient(160deg,#a9c77a,#5f8a35 55%,#3d5d22)"></div>
      <span class="post-date">12 June 2024</span>
      <h3>Lorem ipsum dolor sit amet consectetur adipiscing</h3>
      <p>Lorem ipsum dolor sit amet, conse ctetur adipiscing elit, sed do eiusmod tempor incididunt. laboris nisi ut aliquip ex ea commodo consequat.</p>
      <div class="btn">Read More</div>
    </article>
  </section>

  <!-- Appointment -->
  <section>
    <div class="appt-bg" role="img" aria-label="Faint pale leaf pattern background"></div>
    <div class="appt-box" role="img" aria-label="Dense dark green foliage of leaves"></div>
    <h2 class="section-title" style="top:3406px;color:var(--white);font-weight:500;font-size:34px">Schedule an Appointment</h2>
    <p class="abs" style="left:131px;top:3466px;width:936px;text-align:center;font-weight:600;font-size:18px;line-height:24px;color:var(--white)">Sed ut perspiciatis unde omnis iste natus error sit voluptatem accus<br>antium doloremque laudantium, totam rem aperiam, eaque.</p>
    <div class="btn" style="left:533px;top:3552px;width:133px;height:48px;font-size:15px">Contact Us</div>
  </section>

  <!-- Footer -->
  <footer>
    <div class="foot"></div>
    <svg class="abs" style="left:0;top:3770px" width="1200" height="22" viewBox="0 0 1200 22"><path fill="#f3f4f1" d="M0 0 L1200 0 L1200 9 L1150 15 L1100 7 L1050 13 L1000 8 L950 16 L900 9 L850 14 L800 6 L750 15 L700 10 L650 16 L600 7 L550 14 L500 8 L450 16 L400 9 L350 14 L300 7 L250 15 L200 9 L150 14 L100 7 L50 13 L0 8 Z"/></svg>
    <div class="abs" style="left:131px;top:3858px;display:flex;align-items:center;gap:14px">
      <span style="width:62px;height:62px;background:var(--green)"></span>
      <span style="font-family:'Exo 2',sans-serif;font-weight:700;font-size:30px;line-height:34px;color:var(--white);letter-spacing:1px">Verdell<br>Tree Care</span>
    </div>
    <div class="abs" style="left:502px;top:3841px;width:2px;height:106px;background:var(--white)"></div>

    <div class="abs" style="left:573px;top:3846px;display:flex;gap:22px;align-items:center">
      <div style="width:34px;height:34px;background:var(--white);display:flex;align-items:center;justify-content:center"><svg width="18" height="18" viewBox="0 0 24 24"><path fill="#667473" d="M6.6 10.8a15.1 15.1 0 0 0 6.6 6.6l2.2-2.2c.3-.3.7-.4 1-.2 1.1.4 2.3.6 3.6.6.6 0 1 .4 1 1V20c0 .6-.4 1-1 1A17 17 0 0 1 3 4c0-.6.4-1 1-1h3.5c.6 0 1 .4 1 1 0 1.3.2 2.5.6 3.6.1.3 0 .7-.2 1z"/></svg></div>
      <div style="color:var(--white)"><div style="font-size:11px">CALL US</div><div style="font-family:'Exo 2',sans-serif;font-size:20px">(555) 214 - 7730</div></div>
    </div>
    <div class="abs" style="left:573px;top:3914px;display:flex;gap:22px;align-items:center">
      <div style="width:34px;height:34px;background:var(--white);display:flex;align-items:center;justify-content:center"><svg width="18" height="18" viewBox="0 0 24 24"><path fill="#667473" d="M6.6 10.8a15.1 15.1 0 0 0 6.6 6.6l2.2-2.2c.3-.3.7-.4 1-.2 1.1.4 2.3.6 3.6.6.6 0 1 .4 1 1V20c0 .6-.4 1-1 1A17 17 0 0 1 3 4c0-.6.4-1 1-1h3.5c.6 0 1 .4 1 1 0 1.3.2 2.5.6 3.6.1.3 0 .7-.2 1z"/></svg></div>
      <div style="color:var(--white)"><div style="font-size:11px">CALL US</div><div style="font-family:'Exo 2',sans-serif;font-size:20px">(555) 390 - 6182</div></div>
    </div>

    <div class="abs" role="img" aria-label="Large leafy green tree on a grassy base" style="left:836px;top:3816px;width:301px;height:309px;background:radial-gradient(ellipse at 50% 40%,#4f7a2c 0%,#3d6322 45%,rgba(102,116,115,0) 72%)"></div>

    <div class="abs" style="left:130px;top:3982px;width:650px;height:1px;background:#9aa6a5"></div>
    <span class="foot-nav" style="left:179px">HOME</span>
    <span class="foot-nav" style="left:273px">ABOUT US</span>
    <span class="foot-nav" style="left:406px">SERVICES</span>
    <span class="foot-nav" style="left:539px">BLOG</span>
    <span class="foot-nav" style="left:648px">CONTACT US</span>

    <div class="abs" style="left:135px;top:4074px;display:flex;align-items:center;gap:6px">
      <span style="font-family:'Exo 2',sans-serif;font-size:13px;color:var(--white);margin-right:16px">FOLLOW US</span>
      <span class="social"></span><span class="social"></span><span class="social"></span><span class="social"></span>
    </div>
    <div class="copy">Copyright © 2024 All Rights Reserved</div>
  </footer>

</div>
</body>
</html>
```